Create Website for new company called "Verdale Lodge 37"

Verdale Lodge 37 is a new business situated in Southwestern Colorado. We are creating a business that will rent out spaces where clients can grow their own marijuana. Picture a large green house with partitioned spaces that are secured by a lock. Best way to envision this would be to think of a storage business that rents out storage rooms. The difference is that we will be having the units inside a green house ( for growing purposes) Picture a small area that is secured by locks, Picture an area that has the ability to provide state of the art security, cameras etc. We want to focus our efforts on professionals, blue collar workers and end users of marijuana. Our emphasis is in the area of assisting those whom wish to grow their own plants. We want to provide them a safe facility in which to do that. . Keep in mind that we also build custom grow rooms at clients homes and provide a grow pod (lease these) where a small grow unit will be delivered and picked up from our clients whom want to lease a unit for a short amount of time. We have a business card ( just designed) and will send that information to those whom express an interests in this project. We want to be able to sign people up for our services by entering an agreement and signing the agreement while on the internet. We want to provide our services to those whom consume recreational and medical marijuana. This site will need to gather information I.e email addresses so that we can followup with offers. This is a tremendous opportunity for the right designer. We will be creating many more websites as other states come on line and make marijuana legal to consume. Use the business card model for a point of reference of how we envision the concept. That is a business card we just recently printed. The hands and the plant is our logo so far. Open to suggestions. There will be three levels of service. Bronze, Silver, Gold or Platinum. We will also have a retail biz down the road but not at the present time.

Target Market(s)

Ages 21-60

Industry/Entity Type

Medical

Logo Text

Verdale Lodge 37.

Number of Pages Required

5+ page

Requirements
Must have
• Clean appearance not to busy , easily navigable from link to link, page to page. Must have ability down the road to enter into a contractual agreement via the website. Must use our provided logo and example of that is on our business card that will be uploaded here shortly. We would like to have the colors that are on the business card however if you have suggestions or color schemes that you want us to consider that is okay.
Nice to have
• Nice to have a animation of seed to weed and how clients can save a tremendous amount of money growing their own cannabis. Nice to have testimonial page or feedback page. Have a membership component to website,
Should not have
• No flashing lights, etc. Not to busy in terms of animations.

```html
<!DOCTYPE html>
<html lang="en">
<head>
<meta charset="utf-8">
<title>Verdale Lodge 37</title>
<link rel="stylesheet" href="https://fonts.googleapis.com/css2?family=Oswald:wght@400;500&family=Roboto+Slab:wght@300;400&family=Arimo:wght@400;700&display=swap">
<style>
:root{
  --green:#0b7b3a;
  --green-dark:#06612c;
  --green-light:#2f9a55;
  --grey-bg:#ebebeb;
  --tab-grey:#e6e6e6;
  --ink:#333;
  --muted:#666;
  --slate:#2f3b3d;
  --orange:#e07f34;
  --white:#fff;
}
*{margin:0;padding:0;box-sizing:border-box}
html,body{width:784px;height:1200px;overflow:hidden;background:var(--white)}
body{position:relative;font-family:"Arimo",Arial,sans-serif;color:var(--ink)}
.abs{position:absolute}

/* header */
.ribbon{left:0;top:0;width:784px;height:120px}
.brand{left:272px;top:40px;width:240px;text-align:center;font-family:"Oswald",sans-serif;font-weight:500;font-size:27px;color:var(--slate);letter-spacing:.5px}
.brand-dot{left:380px;top:10px;width:24px;height:24px;border-radius:50%;background:var(--green)}
.nav a{position:absolute;top:78px;font-family:"Oswald",sans-serif;font-size:14px;color:var(--white);text-decoration:none;text-transform:uppercase}
.nav a.lower{text-transform:none}

/* hero */
.hero{left:45px;top:110px;width:694px;height:212px;background:radial-gradient(ellipse at 60% 40%,#6fbf3a 0%,#3f9a2a 45%,#276f22 80%,#1f5a1c 100%)}
.hero-caption{left:82px;top:206px;width:238px;height:76px;background:rgba(255,255,255,.55);border-radius:3px;font-family:"Oswald",sans-serif;font-size:22px;line-height:28px;color:var(--green);text-align:center;padding-top:8px}
.hero-arrow{top:195px;width:14px;height:36px}
.dots span{position:absolute;top:300px;width:14px;height:14px;border-radius:50%;background:#eee;border:2px solid #777}
.dots span.on{background:#333;border-color:#ccc}

/* content area */
.panel{left:45px;top:322px;width:694px;height:600px;background:var(--grey-bg)}
.welcome-title{left:55px;top:328px;font-family:"Roboto Slab",serif;font-weight:300;font-size:17px;color:var(--ink)}
.welcome-title span{color:var(--green)}
.welcome-copy{left:55px;top:352px;width:455px;font-size:8.4px;line-height:12px;color:var(--muted)}
.welcome-copy p{margin-bottom:12px}

.join{left:518px;top:328px;width:215px;height:178px;background:var(--green);border:2px solid var(--green-light);border-radius:4px;text-align:center;color:var(--white)}
.join h2{font-family:"Roboto Slab",serif;font-weight:300;font-size:16px;line-height:18px;margin-top:3px}
.join .field{position:absolute;left:13px;width:191px;height:20px;background:var(--white);font-family:"Roboto Slab",serif;font-size:10px;color:#999;text-align:left;padding:4px 6px}
.join .btn{position:absolute;left:74px;top:112px;width:58px;height:21px;border:1px solid #b9dfc4;background:var(--green);font-family:"Roboto Slab",serif;font-size:12px;line-height:19px}
.join .links{position:absolute;left:0;top:141px;width:100%;font-family:"Roboto Slab",serif;font-size:9.5px}

.rule{left:58px;top:521px;width:668px;height:2px;background:#fafafa}

.section-icon{width:54px;height:54px}
.section-label{left:390px;top:549px;font-family:"Roboto Slab",serif;font-size:16px;color:var(--green);letter-spacing:.3px}

.plan{top:604px;width:219px;height:120px;border:3px solid;border-radius:5px;background:var(--white)}
.plan .tag{position:absolute;top:-10px;left:66px;width:76px;height:28px;font-family:"Oswald",sans-serif;font-size:15px;line-height:26px;color:var(--white);text-align:center}
.plan p{position:absolute;left:14px;top:30px;width:188px;font-size:8.4px;line-height:12px;color:var(--muted);letter-spacing:.3px}
.plan .buy{position:absolute;left:68px;top:79px;width:64px;height:20px;border:1px solid;font-family:"Roboto Slab",serif;font-size:11px;line-height:18px;text-align:center;background:var(--white)}
.plan .buy svg{vertical-align:-2px;margin-right:3px}
.bronze{left:52px;border-color:var(--slate)}
.bronze .tag{background:var(--slate)}
.bronze .buy{color:var(--slate);border-color:var(--slate)}
.silver{left:282px;border-color:var(--green)}
.silver .tag{background:var(--green)}
.silver .buy{color:var(--green);border-color:var(--green)}
.gold{left:510px;border-color:var(--orange)}
.gold .tag{background:var(--orange)}
.gold .buy{color:var(--orange);border-color:var(--orange)}

.feature-title{top:772px;font-family:"Oswald",sans-serif;font-size:15px;color:var(--green)}
.feature-copy{top:860px;width:246px;font-size:8.4px;line-height:12px;color:var(--muted);text-align:right;letter-spacing:.3px}
.feature-img{border-radius:2px}
.divider-v{left:392px;top:740px;width:1px;height:168px;background:var(--green)}

/* news band */
.band{left:45px;top:924px;width:694px;height:178px;background:var(--green);color:var(--white)}
.band h3{position:absolute;font-family:"Roboto Slab",serif;font-weight:300;font-size:16px}
.news-item{position:absolute;left:16px;width:340px;border-bottom:1px solid #d9eadf;font-size:8.4px;line-height:12px}
.news-item .date{font-size:7.5px;line-height:10px}
.follow{left:542px;top:26px;width:142px;height:17px;background:#f2f2f2;border:1px solid #ccc;border-radius:2px;color:#222;font-size:7.6px;line-height:15px;padding-left:22px}
.follow i{position:absolute;left:6px;top:3px;width:10px;height:10px;border-radius:50%;background:#4a9fd8}
.tweet{position:absolute;left:374px;width:314px;font-size:7.6px;line-height:12px}
.tweet .avatar{position:absolute;left:0;top:0;width:46px;height:46px;background:linear-gradient(160deg,#d8cbb9,#9b7d63)}
.tweet .body{position:absolute;left:54px;top:0;width:260px}
.tweet b{font-size:9px}

/* footer */
.footer{left:45px;top:1122px;width:694px;height:78px;background:var(--orange)}
.footer-nav a{position:absolute;top:18px;font-family:"Oswald",sans-serif;font-size:11.5px;color:var(--white);text-decoration:none;text-transform:uppercase}
.footer-nav a.active{color:#111}
.footer-nav a.lower{text-transform:none}
.social{position:absolute;top:9px;width:35px;height:35px;border-radius:50%;border:2px solid}
.copy{position:absolute;left:0;top:56px;width:100%;text-align:center;font-size:7.6px;color:var(--white)}
.copy u{font-weight:700}
</style>
</head>
<body>

<!-- header ribbon -->
<svg class="abs ribbon" viewBox="0 0 784 120" aria-hidden="true">
  <polygon points="24,75 38,75 38,116 24,116 32,96" fill="var(--green-dark)"/>
  <polygon points="760,75 746,75 746,116 760,116 752,96" fill="var(--green-dark)"/>
  <rect x="38" y="68" width="710" height="42" fill="var(--green)"/>
  <polygon points="272,0 512,0 512,68 392,96 272,68" fill="var(--tab-grey)"/>
</svg>
<div class="abs brand-dot"></div>
<div class="abs brand">VERDALE LODGE 37</div>
<nav class="nav">
  <a style="left:70px">Home</a>
  <a style="left:129px">About</a>
  <a style="left:201px">Services</a>
  <a class="lower" style="left:490px">Blog</a>
  <a style="left:550px">Testimonial</a>
  <a style="left:649px">Contact Us</a>
</nav>

<!-- hero -->
<div class="abs hero" role="img" aria-label="Close-up photo of green cannabis leaves"></div>
<div class="abs hero-caption">Supporting the care &amp;<br>cultivation of cannabis</div>
<svg class="abs hero-arrow" style="left:58px" viewBox="0 0 14 36" aria-hidden="true"><polyline points="12,1 2,18 12,35" fill="none" stroke="#fff" stroke-width="1.5"/></svg>
<svg class="abs hero-arrow" style="left:712px" viewBox="0 0 14 36" aria-hidden="true"><polyline points="2,1 12,18 2,35" fill="none" stroke="#fff" stroke-width="1.5"/></svg>
<div class="dots">
  <span class="on" style="left:353px"></span>
  <span style="left:374px"></span>
  <span style="left:395px"></span>
  <span style="left:416px"></span>
</div>

<!-- main panel -->
<div class="abs panel"></div>
<h1 class="abs welcome-title">Welcome to <span>VERDALE LODGE 37</span></h1>
<div class="abs welcome-copy">
  <p>Lorem Ipsum is simply dummy text of the printing and typesetting industry. Lorem Ipsum has been the industry's standard dummy text ever since the 1500s, when an unknown printer took a galley of type and scrambled it to make a type specimen book. It has survived not only five centuries.</p>
  <p>Lorem Ipsum is simply dummy text of the printing and typesetting industry. Lorem Ipsum has been the industry's standard Lorem Ipsum is simply dummy text of the printing and typesetting industry. Lorem Ipsum has been the industry's standard dummy text ever since the 1500s, when an unknown printer took a galley of type and scrambled it to make a type specimen book. It has survived not only five centuries.</p>
  <p>Lorem Ipsum is simply dummy text of the printing and typesetting industry. Lorem Ipsum has been the industry's standard dummy text ever since the 1500s, when an unknown printer took a galley of type and scrambled it to make a type specimen book. It has survived not only five centuries.</p>
</div>

<form class="abs join">
  <h2>A Better Way<br>To Do Business</h2>
  <div class="field" style="top:48px">Enter your name</div>
  <div class="field" style="top:84px">Enter your Email</div>
  <div class="btn">JOIN</div>
  <div class="links">Login &nbsp;|&nbsp; Forget Password</div>
</form>

<div class="abs rule"></div>

<svg class="abs section-icon" style="left:322px;top:530px" viewBox="0 0 54 54" aria-hidden="true">
  <path d="M30,1 A26,26 0 0 1 30,53" fill="none" stroke="var(--green)" stroke-width="1.2"/>
  <circle cx="27" cy="27" r="24" fill="var(--green)"/>
  <circle cx="23" cy="29" r="6" fill="none" stroke="#fff" stroke-width="3.5" stroke-dasharray="2.5 1.6"/>
  <circle cx="23" cy="29" r="2" fill="#fff"/>
  <circle cx="33" cy="21" r="4" fill="none" stroke="#fff" stroke-width="2.5" stroke-dasharray="1.8 1.3"/>
</svg>
<h2 class="abs section-label">SERVICES</h2>

<section class="abs plan bronze">
  <div class="tag">Bronze</div>
  <p>Lorem Ipsum is simply dummy text of the printing and typesetting industry. Lorem Ipsum has been the industry's standard dummy text Lorem Ipsum is simply ever since the 1500s.</p>
  <div class="buy"><svg width="12" height="10" viewBox="0 0 12 10"><path d="M0,0 H2.5 L4,6 H10.5 L12,1.5 H3" fill="none" stroke="currentColor" stroke-width="1.4"/><circle cx="5" cy="8.6" r="1.2" fill="currentColor"/><circle cx="9.5" cy="8.6" r="1.2" fill="currentColor"/></svg>BUY</div>
</section>
<section class="abs plan silver">
  <div class="tag">Silver</div>
  <p>Lorem Ipsum is simply dummy text of the printing and typesetting industry. Lorem Ipsum has been the industry's standard dummy text Lorem Ipsum is simply ever since the 1500s.</p>
  <div class="buy"><svg width="12" height="10" viewBox="0 0 12 10"><path d="M0,0 H2.5 L4,6 H10.5 L12,1.5 H3" fill="none" stroke="currentColor" stroke-width="1.4"/><circle cx="5" cy="8.6" r="1.2" fill="currentColor"/><circle cx="9.5" cy="8.6" r="1.2" fill="currentColor"/></svg>BUY</div>
</section>
<section class="abs plan gold">
  <div class="tag">Gold</div>
  <p>Lorem Ipsum is simply dummy text of the printing and typesetting industry. Lorem Ipsum has been the industry's standard dummy text Lorem Ipsum is simply ever since the 1500s.</p>
  <div class="buy"><svg width="12" height="10" viewBox="0 0 12 10"><path d="M0,0 H2.5 L4,6 H10.5 L12,1.5 H3" fill="none" stroke="currentColor" stroke-width="1.4"/><circle cx="5" cy="8.6" r="1.2" fill="currentColor"/><circle cx="9.5" cy="8.6" r="1.2" fill="currentColor"/></svg>BUY</div>
</section>

<!-- features -->
<svg class="abs section-icon" style="left:59px;top:753px" viewBox="0 0 54 54" aria-hidden="true">
  <path d="M30,1 A26,26 0 0 1 30,53" fill="none" stroke="var(--green)" stroke-width="1.2"/>
  <circle cx="27" cy="27" r="24" fill="var(--green)"/>
  <rect x="16" y="19" width="22" height="16" rx="2" fill="#fff"/>
  <rect x="22" y="16" width="8" height="4" rx="1" fill="#fff"/>
  <circle cx="27" cy="27" r="5" fill="var(--green)"/>
  <circle cx="27" cy="27" r="3" fill="#fff"/>
</svg>
<h3 class="abs feature-title" style="left:125px">Security</h3>
<div class="abs feature-img" style="left:220px;top:744px;width:156px;height:108px;background:linear-gradient(150deg,#f4f4f4,#c9c9c9 70%,#a9a9a9)" role="img" aria-label="Photo of a white outdoor security camera on a wall mount"></div>
<p class="abs feature-copy" style="left:130px">Lorem Ipsum is simply dummy text of the printing and typesetting industry. Lorem Ipsum has been the industry's standard dummy text Lorem Ipsum is simply ever since.</p>

<div class="abs divider-v"></div>

<svg class="abs section-icon" style="left:408px;top:753px" viewBox="0 0 54 54" aria-hidden="true">
  <path d="M30,1 A26,26 0 0 1 30,53" fill="none" stroke="var(--green)" stroke-width="1.2"/>
  <circle cx="27" cy="27" r="24" fill="var(--green)"/>
  <rect x="15" y="17" width="24" height="16" rx="1.5" fill="#fff"/>
  <rect x="18" y="20" width="18" height="10" fill="var(--green)"/>
  <rect x="24" y="33" width="6" height="4" fill="#fff"/>
  <rect x="20" y="37" width="14" height="2" fill="#fff"/>
</svg>
<h3 class="abs feature-title" style="left:474px">Online Access</h3>
<div class="abs feature-img" style="left:570px;top:746px;width:140px;height:106px;background:linear-gradient(160deg,#5a9a3a,#2e6a22 60%,#1a1a1a 100%)" role="img" aria-label="Photo of a desktop monitor showing cannabis leaves"></div>
<p class="abs feature-copy" style="left:478px">Lorem Ipsum is simply dummy text of the printing and typesetting industry. Lorem Ipsum has been the industry's standard dummy text Lorem Ipsum is simply ever since.</p>

<!-- news & tweets -->
<section class="abs band">
  <h3 style="left:16px;top:8px">Latest News</h3>
  <div class="news-item" style="top:40px;height:42px"><div class="date">Dec 17 2014</div>Lorem Ipsum is simply dummy text of the printing and typesetting industry. Lorem Ipsum has been the industry's standard dummy text ever since the 1500s.</div>
  <div class="news-item" style="top:82px;height:45px;padding-top:3px"><div class="date">Dec 14 2014</div>Lorem Ipsum is simply dummy text of the printing and typesetting industry. Lorem Ipsum has been the industry's standard dummy text ever since the 1500s.</div>
  <div class="news-item" style="top:127px;height:40px;padding-top:3px"><div class="date">Dec 10 2014</div>Lorem Ipsum is simply dummy text of the printing and typesetting industry.</div>

  <h3 style="left:374px;top:8px">Tweets</h3>
  <div class="abs" style="left:376px;top:27px;font-size:9.5px">Tweets</div>
  <div class="abs follow"><i></i>Follow @VERDALE LODGE 37</div>

  <div class="tweet" style="top:48px;height:58px;border-bottom:1px solid #d9eadf">
    <div class="avatar" role="img" aria-label="Profile photo of the tweet author"></div>
    <div class="body"><b>Halvora</b> @ Halvora<br>Lorem Ipsum is simply dummy @ dummy text of the printing and typesetting industry. Lorem Ipsum has been the industry's standard<br>Expand</div>
  </div>
  <div class="tweet" style="top:109px;height:56px;border-bottom:1px solid #d9eadf">
    <div class="avatar" role="img" aria-label="Profile photo of the tweet author"></div>
    <div class="body"><b>Halvora</b> @ Halvora<br>Lorem Ipsum is simply dummy @ dummy text of the printing and typesetting industry. Lorem Ipsum has been.<br>Expand</div>
  </div>
</section>

<!-- footer -->
<footer class="abs footer">
  <nav class="footer-nav">
    <a class="active" style="left:25px">Home</a>
    <a style="left:81px">About</a>
    <a style="left:141px">Services</a>
    <a class="lower" style="left:214px">Blog</a>
    <a style="left:266px">Testimonial</a>
    <a style="left:353px">Contact Us</a>
  </nav>
  <span class="social" style="left:546px;background:var(--slate);border-color:#556" aria-label="Social profile"></span>
  <span class="social" style="left:595px;background:var(--green);border-color:#5fb47a" aria-label="Social profile"></span>
  <span class="social" style="left:644px;background:var(--green);border-color:#5fb47a" aria-label="Social profile"></span>
  <div class="copy">© <u>VERDALE LODGE 37</u> - 2014. All Rights Reserved.</div>
</footer>

</body>
</html>
```